BRIGHT RIVER POWER.

I'd like my business logo.
contact name: Dennis Halvorsen
phone:0438759164
email: info@brightriverpower.net.au
website: www.brightriverpower.net.au

services:
solar
battery storage
LED lighting
energy saving solutions
general electrical
I'd like the design to look professional

Target Market(s)

Everyone

Industry/Entity Type

Business

Contact Information for Business Card

as described above

Requirements
Must have
• Id like the colours and the design to work well with my logo.

```html
<!DOCTYPE html>
<html lang="en">
<head>
<meta charset="utf-8">
<title>Bright River Power – Business Card</title>
<link rel="stylesheet" href="https://fonts.googleapis.com/css2?family=Open+Sans:wght@400;600;700&display=swap">
<style>
  :root {
    --canvas: #e9e7e3;
    --orange-light: #fbb03b;
    --orange: #f7941d;
    --orange-deep: #e9841a;
    --green-light: #8cc63f;
    --green: #39b54a;
    --green-deep: #2e9e3e;
    --white: #ffffff;
    --card-shadow: rgba(0, 0, 0, 0.18);
  }
  * { box-sizing: border-box; margin: 0; padding: 0; }
  html, body {
    width: 1200px; height: 843px; overflow: hidden;
    background: var(--canvas);
    font-family: "Open Sans", Arial, sans-serif;
  }
  .stage {
    width: 1200px; height: 843px;
    display: flex; align-items: center; justify-content: center; gap: 60px;
  }
  .card {
    position: relative;
    width: 520px; height: 300px;
    border-radius: 22px;
    overflow: hidden;
    box-shadow: 0 10px 30px var(--card-shadow);
  }

  /* Back side */
  .card-back {
    background: radial-gradient(circle at 45% 35%, var(--orange-light), var(--orange) 55%, var(--orange-deep));
    color: var(--white);
    display: flex; flex-direction: column; align-items: center; justify-content: center;
  }
  .brand { display: flex; align-items: center; gap: 14px; }
  .brand-dot { width: 46px; height: 46px; border-radius: 50%; flex: none; }
  .card-back .brand-dot { background: var(--white); }
  .brand-name { font-weight: 700; font-size: 28px; letter-spacing: 0.5px; line-height: 1; }
  .card-back .brand-name { color: var(--white); }
  .services {
    margin-top: 26px; text-align: center;
    font-size: 12.5px; line-height: 1.7; letter-spacing: 0.3px;
  }

  /* Front side */
  .card-front { background: var(--white); }
  .front-art { position: absolute; inset: 0; }
  .contact { position: absolute; left: 30px; top: 26px; color: var(--white); }
  .contact-name {
    font-weight: 700; font-size: 17px; letter-spacing: 0.6px; text-transform: uppercase;
    margin-bottom: 8px;
  }
  .contact-line {
    display: flex; align-items: center; gap: 8px;
    font-size: 12.5px; line-height: 1.55;
  }
  .contact-line svg { width: 12px; height: 12px; flex: none; }
  .card-front .brand {
    position: absolute; right: 26px; bottom: 40px; width: 190px;
    flex-direction: column; gap: 10px; text-align: center;
  }
  .card-front .brand-dot { background: var(--orange); width: 38px; height: 38px; }
  .card-front .brand-name { color: var(--green); font-size: 24px; line-height: 1.15; }
</style>
</head>
<body>
<main class="stage">

  <section class="card card-back" aria-label="Business card back">
    <div class="brand">
      <span class="brand-dot"></span>
      <span class="brand-name">BRIGHT RIVER POWER</span>
    </div>
    <p class="services">
      Solar • Battery Storage • LED Lighting<br>
      Energy Saving Solutions • General Electrical
    </p>
  </section>

  <section class="card card-front" aria-label="Business card front">
    <svg class="front-art" viewBox="0 0 520 300" preserveAspectRatio="none" aria-hidden="true">
      <defs>
        <radialGradient id="greenFill" cx="0.55" cy="0.45" r="0.7">
          <stop offset="0" stop-color="#8cc63f"/>
          <stop offset="0.6" stop-color="#39b54a"/>
          <stop offset="1" stop-color="#2e9e3e"/>
        </radialGradient>
      </defs>
      <path d="M0,0 H460 C460,70 330,70 300,160 C282,215 260,270 220,300 H0 Z" fill="#f7941d" transform="translate(10,6)"/>
      <path d="M0,0 H460 C460,70 330,70 300,160 C282,215 260,270 220,300 H0 Z" fill="#ffffff" transform="translate(5,4)"/>
      <path d="M0,0 H460 C460,70 330,70 300,160 C282,215 260,270 220,300 H0 Z" fill="url(#greenFill)"/>
    </svg>

    <div class="contact">
      <p class="contact-name">Dennis Halvorsen</p>
      <p class="contact-line">
        <svg viewBox="0 0 24 24"><path fill="#fff" d="M6.6 10.8a15 15 0 0 0 6.6 6.6l2.2-2.2a1 1 0 0 1 1-.25 11.4 11.4 0 0 0 3.6.57 1 1 0 0 1 1 1V20a1 1 0 0 1-1 1A17 17 0 0 1 3 4a1 1 0 0 1 1-1h3.5a1 1 0 0 1 1 1c0 1.25.2 2.45.57 3.6a1 1 0 0 1-.25 1z"/></svg>
        0438759164
      </p>
      <p class="contact-line">
        <svg viewBox="0 0 24 24"><path fill="#fff" d="M2 5h20v14H2z"/><path fill="none" stroke="#39b54a" stroke-width="2" d="M2 6l10 7 10-7"/></svg>
        info@brightriverpower.net.au
      </p>
      <p class="contact-line">
        <svg viewBox="0 0 24 24"><circle cx="12" cy="12" r="10" fill="none" stroke="#fff" stroke-width="2"/><path fill="none" stroke="#fff" stroke-width="1.6" d="M2 12h20M12 2c3 3 3 17 0 20M12 2c-3 3-3 17 0 20"/></svg>
        www.brightriverpower.net.au
      </p>
    </div>

    <div class="brand">
      <span class="brand-dot"></span>
      <span class="brand-name">BRIGHT RIVER<br>POWER</span>
    </div>
  </section>

</main>
</body>
</html>
```